Tampa Bay fishing guide needs stunning website.

I currently have a site - www.reelcoveguide.net which I personally put together using the Pagely platform and I am looking for a redesign on a different platform (Sitecraft?) that will allow me to easily create landing pages in the future. Would like to have a block for visitors to opt in to newsletter. Need social media links on all pages.

I would like to let my visitors know that I am able to handle their fishing charter needs here in the Tampa Bay area, if I'm not available for the dates they are looking to go I can refer them to a reputable captain in the area.

Target Market(s)

United States

Industry/Entity Type

Tourism

Coding

Coded - Design and coding required

Number of Pages Required

5+ page

Font styles to use
Sans Serif

Colors
0355a3
3176b5
85abd2
fbf289

Requirements
Must have
• Mobile Responsive, Ability to insert Vantor Metrics, Chatterbox pixels, ability to add custom landing pages in future
Nice to have
• Clean, easy navigation

```html
<!DOCTYPE html>
<html lang="en">
<head>
<meta charset="utf-8">
<title>Capt. Wade Harlan – Tampa Bay Fishing Charters</title>
<link href="https://fonts.googleapis.com/css2?family=Courgette&family=PT+Sans:wght@400;700&display=swap" rel="stylesheet">
<style>
:root{
  --deep:#0355a3;
  --mid:#3176b5;
  --pale:#85abd2;
  --sun:#fbf289;
  --navy:#0a3f7d;
  --ink:#555d66;
  --white:#ffffff;
  --script:"Courgette", cursive;
  --sans:"PT Sans", sans-serif;
}
*{box-sizing:border-box;margin:0;padding:0}
html,body{width:1200px;height:3422px;overflow:hidden}
body{font-family:var(--sans);color:var(--ink);background:var(--white);position:relative}
section,header,footer{position:absolute;left:0;width:1200px;overflow:hidden}
.abs{position:absolute}
.script{font-family:var(--script);font-weight:400}

/* header / hero */
.hero{top:0;height:700px}
.hero-bg{position:absolute;inset:0;background:linear-gradient(180deg,#cfe6f7 0%,#7fb7e4 18%,#2f86cf 33%,#0a5fb3 55%,#06488f 80%,#0c5aa3 100%)}
.hero-photo{position:absolute;left:640px;top:170px;width:560px;height:480px;border-radius:40% 0 0 0;background:radial-gradient(ellipse at 50% 40%,rgba(40,90,190,.9),rgba(10,70,150,0) 70%)}
.follow{left:80px;top:40px;color:var(--white);font-size:17px}
.social{display:flex;gap:10px}
.social span{display:inline-block;padding:0 12px;height:40px;line-height:40px;border-radius:20px;background:var(--sun);color:var(--deep);font-size:14px;font-weight:700;white-space:nowrap}
.top-social{left:80px;top:76px}
.brand{left:0;width:1200px;top:62px;text-align:center;font-family:var(--script);font-size:52px;color:var(--deep)}
.call{left:900px;top:46px;color:var(--white)}
.call small{display:block;font-size:18px;padding-left:48px}
.call strong{display:block;font-size:30px;color:var(--sun);font-weight:400;padding-left:48px;letter-spacing:1px}
.call svg{position:absolute;left:0;top:6px}
.nav{left:205px;top:160px;display:flex;font-size:16px;color:#1d2f4a;letter-spacing:.3px}
.nav a{color:inherit;text-decoration:none;padding:0 22px;height:52px;line-height:52px}
.nav a.current{background:var(--sun);color:var(--deep);padding:0 26px}
.hero-title{left:80px;top:335px;width:720px;font-size:36px;line-height:52px;color:var(--white)}
.dots{left:80px;top:500px;display:flex;gap:7px}
.dots i{width:12px;height:12px;border-radius:50%;border:2px solid var(--white)}
.dots i.on{background:var(--sun);border-color:var(--sun)}
.wave{position:absolute;left:0;bottom:0}

/* intro */
.intro{top:700px;height:447px;background:#f1f5f9}
.section-title{font-family:var(--script);color:var(--deep);font-size:40px;line-height:54px;text-align:center}
.intro .section-title{position:absolute;left:250px;width:700px;top:40px}
.intro p{position:absolute;left:150px;width:900px;text-align:center;font-size:14.5px;line-height:26px}
.btn{display:inline-block;font-family:var(--script);font-size:20px;text-align:center;line-height:54px;height:54px;width:155px;background:var(--sun);color:var(--deep);text-decoration:none}
.btn.outline{background:transparent;border:2px solid var(--sun);color:var(--sun);line-height:50px}

/* about */
.about{top:1147px;height:416px;background:linear-gradient(180deg,#0a4f98,#08468a 60%,#0b549e)}
.about h2{left:80px;top:58px;color:var(--sun);font-size:40px}
.about .copy{left:80px;top:115px;width:700px;color:var(--white);font-size:13.8px;line-height:28px}
.about-art{left:800px;top:95px;width:330px;height:180px;background:linear-gradient(135deg,rgba(133,171,210,.28),rgba(49,118,181,.18))}

/* testimonials */
.testi{top:1563px;height:371px;background:var(--sun)}
.testi .section-title{position:absolute;top:50px;width:1200px}
.testi .lead{left:200px;width:800px;top:120px;text-align:center;font-size:16px;line-height:26px;color:#333}
.arrow{width:42px;height:42px;border-radius:50%;border:2px solid #9a9b7a;top:175px}
.arrow svg{position:absolute;left:11px;top:11px}
.qmark{left:0;width:1200px;top:182px;text-align:center;font-size:96px;line-height:80px;color:var(--deep);font-family:Georgia,serif;font-weight:700}
.quote{left:0;width:1200px;top:245px;text-align:center;font-size:19px;color:#333}
.cite{left:0;width:1200px;top:285px;text-align:center;font-size:17px;color:var(--deep)}

/* rates */
.rates{top:1934px;height:575px;background:linear-gradient(180deg,#0a2f5e,#0b4c92 45%,#0f5ea8 75%,#0b4d92)}
.rates h2{left:0;width:1200px;top:60px;text-align:center;color:var(--sun);font-size:40px}
.rate{width:260px;text-align:center;top:140px}
.rate .pic{width:178px;height:178px;border-radius:50%;border:4px solid var(--sun);margin:0 auto;background:radial-gradient(circle at 50% 40%,#8fb8d8,#3f7aa8 60%,#1d4a78)}
.rate h3{font-family:var(--script);font-weight:400;color:var(--white);font-size:21px;line-height:31px;margin-top:26px;height:98px}
.rate .btn{margin-top:10px}

/* pickup + contact */
.meet{top:2509px;height:600px;background:#f1f5f9}
.meet h2{font-family:var(--script);color:var(--deep);font-size:38px;font-weight:400}
.meet .lead{font-size:13px;line-height:22px;color:#444}
.divider{left:570px;top:70px;width:2px;height:470px;background:#dde4ec}
.spot{left:80px;display:flex;gap:26px;align-items:flex-start}
.spot h4{font-family:var(--script);font-weight:400;color:var(--deep);font-size:20px}
.spot p{font-size:13px;color:#444;margin-top:4px}
.field{left:614px;width:490px;height:45px;border:1.5px solid #b9c6d6;background:var(--white);border-radius:3px;font-size:13px;color:#444;padding:12px 14px}
.field.focus{border-color:var(--mid)}
.field.area{height:94px}

/* footer */
.foot{top:3102px;height:251px;background:linear-gradient(180deg,#0b5aa8,#0a4e96 60%,#0a4688)}
.foot h5{font-family:var(--script);font-weight:400;color:var(--sun);font-size:19px;top:80px}
.foot .line{color:var(--white);font-size:13px;display:flex;gap:12px;align-items:center}
.cards{left:344px;top:130px;display:flex;gap:6px}
.cards span{height:36px;padding:0 7px;line-height:36px;background:var(--white);border-radius:3px;font-size:12px;font-weight:700;color:var(--deep)}
.foot-social{left:609px;top:130px;gap:6px}
.foot-social span{height:36px;line-height:36px;padding:0 9px;font-size:12px}
.news{left:858px;top:118px;width:246px;height:42px;background:#eef1f4;font-size:13px;color:#666;padding:12px}
.sub{left:858px;top:166px;width:162px;height:42px;background:var(--sun);color:var(--deep);font-family:var(--script);font-size:18px;text-align:center;line-height:42px}
.copyright{left:0;width:1200px;top:3353px;height:69px;background:var(--sun);text-align:center;line-height:69px;font-size:14px;color:#333}
</style>
</head>
<body>

<header class="hero">
  <div class="hero-bg" role="img" aria-label="Bright sky over Tampa Bay water fading into an underwater reef scene"></div>
  <div class="hero-photo" role="img" aria-label="Photo of the captain holding a large snook"></div>

  <div class="abs follow">Follow Us On</div>
  <div class="abs social top-social"><span>Chatterbox</span><span>Chirpline</span><span>Circlo</span></div>

  <div class="abs brand">Capt. Wade Harlan</div>

  <div class="abs call">
    <svg width="36" height="36" viewBox="0 0 24 24" aria-hidden="true"><path fill="#fbf289" d="M6.6 10.8a15.1 15.1 0 0 0 6.6 6.6l2.2-2.2a1 1 0 0 1 1-.25 11.4 11.4 0 0 0 3.6.57 1 1 0 0 1 1 1V20a1 1 0 0 1-1 1A17 17 0 0 1 3 4a1 1 0 0 1 1-1h3.5a1 1 0 0 1 1 1c0 1.250.2 2.45.57 3.6a1 1 0 0 1-.25 1z"/></svg>
    <small>Call Us Now</small>
    <strong>555 014 2290</strong>
  </div>

  <nav class="abs nav">
    <a class="current" href="#">HOME</a>
    <a href="#">ABOUT US</a>
    <a href="#">PICK UP LOCATION</a>
    <a href="#">RATES</a>
    <a href="#">CONTACT US</a>
    <a href="#">GIFT CARD</a>
  </nav>

  <h1 class="abs hero-title script">Come with fishing guide, Tampa Bay fishing charter most respected Captain, 25 year Native Guide</h1>
  <div class="abs dots"><i></i><i></i><i class="on"></i><i></i></div>

  <svg class="wave" width="1200" height="90" viewBox="0 0 1200 90" aria-hidden="true">
    <path d="M0 30 Q300 90 600 55 T1200 20 L1200 90 L0 90Z" fill="#f1f5f9"/>
    <path d="M0 30 Q300 90 600 55 T1200 20" fill="none" stroke="#fbf289" stroke-width="6"/>
  </svg>
</header>

<section class="intro">
  <h2 class="section-title">Tampa Bay, Fishing Guid, Tampa Bay Fishing Charters</h2>
  <p style="top:160px">Capt. Wade Harlan, with over 20 years' experience, Native fishing charter tampa charter captain offering full and half day fishing charters on the waters of Tampa Bay. If you're looking for a great fishing charter tampa don't hesitate to contact Capt. Wade or you can simply book your trip online here.</p>
  <p style="top:240px">Come enjoy a wonderful day fishing charters Tampa for Tarpon, Snook, Redfish, Trout, Sharks, Cobia, Spanish mackerel as well as others aboard Capt. Wade Harlan Sport fishing Charters boat. Capt. Wade will work hard to ensure that you and your guests have a memorable day enjoying the wonderful gamefish that Tampa Bay has to offer.</p>
  <a class="btn abs" href="#" style="left:522px;top:331px">Know More</a>
</section>

<section class="about">
  <h2 class="abs script">About Capt. Wade Harlan</h2>
  <div class="abs copy">
    <p>Capt. Wade was born and raised in the Tampa Bay area and fell in love with fishing as a very young boy. He has guided some of the world's top name celebrities and politicians. Through his passion and hard work he has earned a living as a full time guide in the Tampa Bay area for over 25 years.</p>
    <p style="margin-top:8px">Capt. Wade invites you and your guests to come aboard and enjoy the thrills of fishing for the top gamefish that Tampa Bay has to offer. Capt. Wade promises to use his life long experience to put you on the fish here in the Tampa Bay area. He looks forward to meeting you and your guests. Book your trip of a lifetime today.</p>
  </div>
  <div class="abs about-art" role="img" aria-label="Illustration of a gamefish from Tampa Bay"></div>
  <a class="btn abs" href="#" style="left:80px;top:294px">Know More</a>
</section>

<section class="testi">
  <h2 class="section-title">Testimonials</h2>
  <p class="abs lead">Over the many years we have had the pleasure of working with a lot different people, please take a look below and see what they have to say about us.</p>
  <div class="abs arrow" style="left:77px"><svg width="16" height="16" viewBox="0 0 16 16" aria-hidden="true"><path d="M10 3 5 8l5 5" fill="none" stroke="#777" stroke-width="2"/></svg></div>
  <div class="abs arrow" style="left:1081px"><svg width="16" height="16" viewBox="0 0 16 16" aria-hidden="true"><path d="M6 3l5 5-5 5" fill="none" stroke="#777" stroke-width="2"/></svg></div>
  <div class="abs qmark">&ldquo;</div>
  <p class="abs quote">&ldquo; Congratulations on winning the Gulf Coast Celebrity Grand Slam Tournament &rdquo;</p>
  <p class="abs cite script">Dana Whitfield, Former State Senator</p>
</section>

<section class="rates">
  <div class="abs" style="inset:0;background:rgba(10,60,120,.25)" role="img" aria-label="Darkened photo of a charter boat on the bay"></div>
  <h2 class="abs script">Our Rates</h2>
  <div class="abs rate" style="left:73px">
    <div class="pic" role="img" aria-label="Anglers holding a snook on the boat"></div>
    <h3>Half Day (4 hour) Charter 1-3 people $399, 4 people $499</h3>
    <a class="btn" href="#">Book Now !</a>
  </div>
  <div class="abs rate" style="left:333px">
    <div class="pic" role="img" aria-label="Couple showing their catch"></div>
    <h3>3/4 Day (6 hour) Charter 1-3 people $499, 4 people $599</h3>
    <a class="btn outline" href="#">Book Now !</a>
  </div>
  <div class="abs rate" style="left:600px">
    <div class="pic" role="img" aria-label="Anglers landing a fish over green water"></div>
    <h3>Full Day (8 hours) Charter 1-3 people $599, 4 people $699</h3>
    <a class="btn outline" href="#">Book Now !</a>
  </div>
  <div class="abs rate" style="left:867px">
    <div class="pic" role="img" aria-label="Guests holding a redfish"></div>
    <h3>Half Day (4 hour) Charter 1-3 people $399, 4 people $499</h3>
    <a class="btn outline" href="#">Book Now !</a>
  </div>
</section>

<section class="meet">
  <h2 class="abs" style="left:80px;top:50px">Pick Up Location</h2>
  <p class="abs lead" style="left:80px;top:112px;width:470px">Four Convenient Locations on Every Corner of Tampa Bay No matter where you might be staying in the Tampa Bay area, Capt. Wade can pick you up nearby.</p>

  <div class="abs spot" style="top:200px">
    <svg width="50" height="48" viewBox="0 0 50 48" aria-hidden="true"><path d="M24 2v34H4z" fill="#0355a3"/><path d="M27 10v26h16z" fill="#0355a3"/><path d="M2 39h46l-6 7H8z" fill="#0355a3"/></svg>
    <div><h4>Pelican Point Marina</h4><p>4820 Bayside Road South, St. Petersburg, FL 33700</p></div>
  </div>
  <div class="abs spot" style="top:284px">
    <svg width="50" height="48" viewBox="0 0 50 48" aria-hidden="true"><path d="M24 2v34H4z" fill="#4a4f55"/><path d="M27 10v26h16z" fill="#4a4f55"/><path d="M2 39h46l-6 7H8z" fill="#4a4f55"/></svg>
    <div><h4>Heron Cove - Ruskin</h4><p>218 Saltmarsh Ln Ruskin, FL 33500</p></div>
  </div>
  <div class="abs spot" style="top:366px">
    <svg width="50" height="48" viewBox="0 0 50 48" aria-hidden="true"><path d="M24 2v34H4z" fill="#4a4f55"/><path d="M27 10v26h16z" fill="#4a4f55"/><path d="M2 39h46l-6 7H8z" fill="#4a4f55"/></svg>
    <div><h4>Bridgeview Boat Ramp</h4><p>3902 W Causeway Blvd Tampa, FL 33600</p></div>
  </div>
  <div class="abs spot" style="top:450px">
    <svg width="50" height="48" viewBox="0 0 50 48" aria-hidden="true"><path d="M24 2v34H4z" fill="#4a4f55"/><path d="M27 10v26h16z" fill="#4a4f55"/><path d="M2 39h46l-6 7H8z" fill="#4a4f55"/></svg>
    <div><h4>Tarpon Flats Boat Ramp</h4><p>916 Seagrass Ave Holmes Beach, FL 34200</p></div>
  </div>

  <div class="abs divider"></div>

  <h2 class="abs" style="left:611px;top:50px">Contact Us</h2>
  <p class="abs lead" style="left:614px;top:112px;width:500px">Please fell free to reach out to Capt. Wade with any questions you might have. Just simply fill out the form to the left and he will get back with you as soon as he gets off the water.</p>
  <div class="abs field focus" style="top:191px">Name *</div>
  <div class="abs field" style="top:244px">Email *</div>
  <div class="abs field" style="top:297px">Phone *</div>
  <div class="abs field area" style="top:347px">Message *</div>
  <a class="btn abs" href="#" style="left:782px;top:449px">Submit</a>
</section>

<footer class="foot">
  <svg class="abs" style="left:0;top:0" width="1200" height="60" viewBox="0 0 1200 60" aria-hidden="true">
    <path d="M0 0H1200V10Q900 55 600 40T0 10Z" fill="#f1f5f9"/>
    <path d="M0 10Q300 25 600 40T1200 10" fill="none" stroke="#fbf289" stroke-width="6"/>
  </svg>

  <h5 class="abs" style="left:80px">Get In Touch</h5>
  <div class="abs line" style="left:80px;top:128px">
    <svg width="20" height="20" viewBox="0 0 24 24" aria-hidden="true"><path fill="none" stroke="#fff" stroke-width="1.8" d="M6.6 10.8a15.1 15.1 0 0 0 6.6 6.6l2.2-2.2 4.6 1.3V20A17 17 0 0 1 3 4h4.5l1.3 4.6z"/></svg>555-010-4471</div>
  <div class="abs line" style="left:80px;top:162px">
    <svg width="20" height="16" viewBox="0 0 20 16" aria-hidden="true"><rect x="1" y="1" width="18" height="14" fill="none" stroke="#fff" stroke-width="1.6"/><path d="M1 1l9 7 9-7" fill="none" stroke="#fff" stroke-width="1.6"/></svg>captwade@harborpost.net</div>

  <h5 class="abs" style="left:344px">We Accept</h5>
  <div class="abs cards"><span>Paywell</span><span>Tallycard</span><span>Versa</span><span>Amberpass</span></div>

  <h5 class="abs" style="left:609px">Follow Us On</h5>
  <div class="abs social foot-social"><span>Chatterbox</span><span>Chirpline</span><span>Circlo</span></div>

  <h5 class="abs" style="left:858px">Newsletter</h5>
  <div class="abs news">Enter Email Id</div>
  <div class="abs sub">Subscribe</div>
</footer>

<div class="abs copyright">©<strong>Capt. Wade Harlan</strong>- 2016. All Rights Reserved</div>

</body>
</html>
```